Theatre Company needs a Poster design for a world premiere of "The Lantern" Play.

We are premiering a play that celebrates community in rural and regional Australia . We need a poster for A3 and A5 size and an image that can be used in our email correspondence/webpage.

Attached is some ideas the producing theatre committee has come up with, a river runs through the town itself.

Town

```html
<!DOCTYPE html>
<html lang="en">
<head>
<meta charset="utf-8">
<title>The Lantern — Poster</title>
<link rel="stylesheet" href="https://fonts.googleapis.com/css2?family=Bodoni+Moda:opsz,wght@6..96,400&family=Libre+Caslon+Text:wght@400;700&display=swap">
<style>
  :root {
    --sky-light: #e3f0f0;
    --sky-mid: #b9c8ca;
    --cloud-grey: #909d9e;
    --land-dark: #3b4242;
    --water-dark: #1d2222;
    --seal-red: rgba(201, 60, 72, 0.93);
    --banner-red: #c23a46;
    --rule-light: #ece8e8;
    --ink-white: #ffffff;
  }
  * { margin: 0; padding: 0; box-sizing: border-box; }
  html, body { width: 849px; height: 1200px; overflow: hidden; background: #ffffff; }
  .poster {
    position: relative;
    width: 849px;
    height: 1200px;
    overflow: hidden;
  }
  .riverside-scene {
    position: absolute;
    inset: 0;
    background:
      radial-gradient(ellipse 60% 25% at 80% 80%, rgba(30,35,35,0.55), transparent 70%),
      linear-gradient(180deg,
        var(--sky-light) 0%,
        var(--sky-mid) 38%,
        var(--cloud-grey) 62%,
        var(--land-dark) 74%,
        #4a5252 80%,
        var(--water-dark) 100%);
  }
  .title-seal {
    position: absolute;
    left: 24px;
    top: 87px;
    width: 644px;
    height: 644px;
    border-radius: 50%;
    background: var(--seal-red);
  }
  .seal-rule {
    position: absolute;
    left: 31px;
    width: 628px;
    height: 5px;
    background: var(--rule-light);
  }
  .seal-rule--top { top: 338px; }
  .seal-rule--bottom { top: 477px; }
  .presenter {
    position: absolute;
    left: 31px;
    width: 628px;
    top: 292px;
    text-align: center;
    font-family: "Libre Caslon Text", serif;
    font-size: 20px;
    line-height: 26px;
    letter-spacing: 0.3px;
    color: var(--ink-white);
    text-transform: uppercase;
    white-space: nowrap;
  }
  .play-title {
    position: absolute;
    left: 31px;
    width: 628px;
    top: 358px;
    text-align: center;
    font-family: "Bodoni Moda", serif;
    font-weight: 400;
    font-size: 76px;
    line-height: 100px;
    letter-spacing: 1px;
    color: var(--ink-white);
    text-transform: uppercase;
    white-space: nowrap;
  }
  .playwright {
    position: absolute;
    right: 232px;
    top: 505px;
    font-family: "Libre Caslon Text", serif;
    font-weight: 700;
    font-size: 17px;
    line-height: 22px;
    letter-spacing: 0.3px;
    color: var(--ink-white);
    text-transform: uppercase;
    white-space: nowrap;
  }
  .tagline-band {
    position: absolute;
    left: 233px;
    top: 1099px;
    width: 602px;
    height: 72px;
    background: var(--banner-red);
    border-top: 3px solid var(--banner-red);
    box-shadow: inset 0 5px 0 -2px var(--rule-light);
    display: flex;
    align-items: center;
    justify-content: center;
  }
  .tagline {
    font-family: "Libre Caslon Text", serif;
    font-size: 27px;
    color: var(--ink-white);
    padding-top: 4px;
    white-space: nowrap;
  }
</style>
</head>
<body>
  <main class="poster">
    <div class="riverside-scene" role="img" aria-label="Black and white photograph of a still river bank with reeds, bare trees and a wooden boathouse under a cloudy sky"></div>

    <div class="title-seal"></div>
    <p class="presenter">Merrigal Theatre Company presents to you</p>
    <div class="seal-rule seal-rule--top"></div>
    <h1 class="play-title">The Lantern</h1>
    <div class="seal-rule seal-rule--bottom"></div>
    <p class="playwright">Written by Ness Calloway</p>

    <div class="tagline-band">
      <p class="tagline">“a river runs through the town itself”</p>
    </div>
  </main>
</body>
</html>
```